Heron Haulage needs Bussiness cards!

Our new trucking company needs business cards!
We need the same design with two different names and emails, everything else it's the same.
I have included our original logo so we can use it for the design.
Note: the logo to be used is the o e with the buffalo on the right side, next to the letters H and H.

Target Market(s)

Trucking, refrigerated transportation, freight

Industry/Entity Type

Business

Contact Information for Business Card

Card #1:
Marcus Whitfield
marcuswhitfield@heronhaulage.example
1-855-317-6094
(555)238-7160
4117 W. Larkin Ave.
Alder Springs, OK 78590
www.heronhaulage.example

Card#2:
Rosalba Quintero
rosalba@heronhaulage.example
1-855-317-6094
(555)238-7160
4117 W. Larkin Ave.
Alder Springs, OK 78590
www.heronhaulage.example

Font styles to use
Sans Serif

Colors
0655a3
ec1f27
ffffff

Requirements
Must have
• our logo
Nice to have
• roads on background,

```html
<!DOCTYPE html>
<html lang="en">
<head>
<meta charset="utf-8">
<title>Heron Haulage – Business Card</title>
<link rel="stylesheet" href="https://fonts.googleapis.com/css2?family=Source+Sans+3:wght@400;600;700;900&display=swap">
<style>
  :root {
    --navy: #0d2f5c;
    --red: #c8161d;
    --white: #ffffff;
    --page: #eceae6;
    --ink: #14335f;
    --sky: #8fc2e8;
    --hill: #5e8a3c;
    --road: #5d6466;
  }
  * { margin: 0; padding: 0; box-sizing: border-box; }
  html, body { width: 1200px; height: 900px; overflow: hidden; }
  body {
    background: var(--page);
    font-family: "Source Sans 3", "Myriad Pro", Arial, sans-serif;
    position: relative;
  }
  .card {
    position: absolute;
    left: 270px;
    width: 660px;
    height: 377px;
    background: var(--white);
    overflow: hidden;
    box-shadow: 0 2px 10px rgba(0,0,0,0.12);
  }
  .card--front { top: 50px; }
  .card--back { top: 473px; }

  /* Front: road photo with company name */
  .front-photo {
    position: absolute; inset: 0;
    background:
      linear-gradient(180deg, var(--sky) 0%, #bcd9ee 28%, #7fa55a 42%, var(--hill) 58%, #4c5a4a 70%, var(--road) 100%);
  }
  .front-name {
    position: absolute;
    left: 300px; top: 120px;
    color: var(--white);
    font-weight: 900;
    font-size: 64px;
    line-height: 0.9;
    letter-spacing: -1px;
  }

  /* Back: contact details */
  .corner-mark { position: absolute; left: 0; top: 0; }
  .holder-name {
    position: absolute;
    left: 80px; top: 30px;
    font-size: 21px;
    font-weight: 600;
    color: var(--ink);
  }
  .holder-name .first { color: var(--red); }
  .contact {
    position: absolute;
    left: 56px; top: 132px;
    list-style: none;
    font-size: 15px;
    line-height: 21px;
    color: var(--ink);
  }
  .contact .address { margin-bottom: 4px; }
  .contact li { display: flex; align-items: center; gap: 8px; }
  .contact li.address { display: block; padding-left: 19px; }
  .contact svg { width: 11px; height: 11px; flex: none; }
  .brand {
    position: absolute;
    right: 50px; top: 138px;
    display: flex; align-items: center; gap: 12px;
    color: var(--navy);
    font-weight: 900;
    font-size: 40px;
    line-height: 1;
    letter-spacing: -0.5px;
  }
  .brand .dot {
    width: 16px; height: 16px; border-radius: 50%;
    background: var(--navy);
  }
  .bands { position: absolute; left: 0; bottom: 0; }
</style>
</head>
<body>

  <section class="card card--front" aria-label="Card front">
    <div class="front-photo" role="img" aria-label="Blurred photo of a country road winding through green hills under a blue sky"></div>
    <div class="front-name">Heron<br>Haulage</div>
  </section>

  <section class="card card--back" aria-label="Card back">
    <svg class="corner-mark" width="70" height="42" viewBox="0 0 70 42" aria-hidden="true">
      <polygon points="0,0 40,0 0,42" fill="var(--red)"/>
      <polygon points="44,0 70,0 70,42 8,42" fill="var(--navy)"/>
    </svg>

    <h1 class="holder-name"><span class="first">Marcus</span> Whitfield</h1>

    <ul class="contact">
      <li class="address">4117 W. Larkin Ave.<br>Alder Springs, OK 78590</li>
      <li>
        <svg viewBox="0 0 12 12"><rect x="3" y="0.5" width="6" height="11" rx="1" fill="none" stroke="var(--red)" stroke-width="1.4"/></svg>
        (555)238-7160
      </li>
      <li>
        <svg viewBox="0 0 12 12"><path d="M2 1 L4.5 1 L5.5 3.8 L4 5 Q5 7.2 7 8 L8.2 6.5 L11 7.5 L11 10 Q5 11 1 3 Z" fill="var(--red)"/></svg>
        1-855-317-6094
      </li>
      <li>
        <svg viewBox="0 0 12 12"><rect x="0.5" y="2" width="11" height="8" fill="var(--red)"/><path d="M0.5 2 L6 6.5 L11.5 2" fill="none" stroke="var(--white)" stroke-width="1"/></svg>
        marcuswhitfield@heronhaulage.example
      </li>
      <li>
        <svg viewBox="0 0 12 12"><circle cx="6" cy="6" r="5.5" fill="var(--red)"/><path d="M0.5 6 H11.5 M6 0.5 Q3 6 6 11.5 M6 0.5 Q9 6 6 11.5" fill="none" stroke="var(--white)" stroke-width="0.8"/></svg>
        www.heronhaulage.example
      </li>
    </ul>

    <div class="brand"><span class="dot"></span>Heron Haulage</div>

    <svg class="bands" width="660" height="80" viewBox="0 0 660 80" aria-hidden="true">
      <polygon points="0,22 300,22 290,44 0,44" fill="var(--red)"/>
      <polygon points="292,44 660,44 660,80 276,80" fill="var(--navy)"/>
    </svg>
  </section>

</body>
</html>
```